Tidewell Comforts, a portable luxury restroom trailer company needs a landing page

We need a landing page for a luxury portable restroom trailer company. This should be modern, and simple - use any combination of Pantone colors: Warm Gray 1C, Black 7C, 7529c, 873C, 8003C

We rent these trailers for special events like weddings, private parties, festivals, family reunions, team building, wine tastings, beer tastings, food truck round-ups, etc.

An idea of the landing page is in the files below. Please use stock photography and placeholder text for now. The winning design will be given final content.

Requirements
Must have
• Multiple "Get Quote" buttons or a place for them to type in type of rental, how many people etc

```html
<!DOCTYPE html>
<html lang="en">
<head>
<meta charset="utf-8">
<title>Tidewell Comforts – Luxury Restroom Trailers</title>
<link href="https://fonts.googleapis.com/css2?family=Poppins:wght@400;500;600;700&family=Roboto:wght@500;700&display=swap" rel="stylesheet">
<style>
:root{
  --blue:#2a87d7;
  --blue-deep:#1f6fc0;
  --ink:#111111;
  --text:#333333;
  --muted:#555555;
  --hero-bg:#eef6fd;
  --section-gray:#f6f6f6;
  --line:#e6e6e6;
  --footer:#1b1b1b;
  --white:#ffffff;
}
*{box-sizing:border-box;margin:0;padding:0}
html,body{width:1200px;height:3844px;overflow:hidden}
body{position:relative;font-family:"Poppins",sans-serif;color:var(--text);background:var(--white)}
.abs{position:absolute}
.btn{position:absolute;display:flex;align-items:center;justify-content:center;background:var(--blue);color:var(--white);font:600 15px "Poppins",sans-serif;text-transform:uppercase;border-radius:3px}
.brand{font-weight:600;color:var(--ink)}
.brand span{color:var(--blue);font-weight:400}

/* header */
.site-header{position:absolute;left:0;top:0;width:1200px;height:88px;background:var(--hero-bg)}
.logo{position:absolute;left:98px;top:18px;font-size:34px;letter-spacing:.3px}
.nav{position:absolute;top:33px;font:500 15px "Poppins",sans-serif;color:var(--ink)}
.nav.active{color:var(--blue)}

/* hero */
.hero{position:absolute;left:0;top:88px;width:1200px;height:726px;background:var(--hero-bg)}
.tile{position:absolute;width:228px;height:231px}
.hero-copy{position:absolute;left:243px;top:246px;width:714px;text-align:center}
.hero-title{font-size:64px;line-height:1;color:var(--ink);font-weight:600}
.hero-title span{color:var(--blue);font-weight:400}
.hero-text{margin-top:28px;font-size:15px;line-height:24px;color:var(--ink)}

/* sections */
.section-title{position:absolute;left:0;width:1200px;text-align:center;font-size:39px;font-weight:600;color:var(--ink)}
.section-title span{color:var(--blue);font-weight:400}

.event-card{position:absolute;top:955px;width:322px;height:409px;background:var(--white);box-shadow:0 0 6px rgba(0,0,0,.12)}
.event-photo{position:absolute;left:0;top:0;width:322px;height:237px}
.event-icon{position:absolute;left:119px;top:195px;width:84px;height:84px;border-radius:50%;background:var(--blue);border:5px solid #cfe4f7;display:flex;align-items:center;justify-content:center}
.event-name{position:absolute;left:0;top:288px;width:322px;text-align:center;font:500 25px "Roboto",sans-serif;color:var(--ink)}
.event-text{position:absolute;left:20px;top:327px;width:282px;text-align:center;font-size:12.5px;line-height:21px;color:var(--ink)}
.arrow{position:absolute;top:1145px}

.products{position:absolute;left:0;top:1548px;width:1200px;height:1228px;background:var(--section-gray)}
.product-card{position:absolute;left:100px;width:1000px;height:303px;background:var(--white);box-shadow:0 0 4px rgba(0,0,0,.08)}
.product-name{position:absolute;left:31px;top:30px;font:700 30px "Roboto",sans-serif;color:var(--ink)}
.product-text{position:absolute;left:31px;top:79px;width:548px;font-size:14.5px;line-height:24.3px;text-align:justify;color:var(--muted)}
.product-photo{position:absolute;left:640px;top:7px;width:353px;height:289px}
.product-card .btn{left:31px;top:221px;width:156px;height:46px;font-size:14px}

/* contact */
.contact{position:absolute;left:0;top:2776px;width:1200px;height:779px;background:linear-gradient(180deg,#2f8ee0 0%,#2a86d6 55%,#2b87d8 100%)}
.contact-title{position:absolute;left:0;top:58px;width:1200px;text-align:center;font-size:39px;font-weight:500;color:var(--white)}
.field{position:absolute;height:59px;background:var(--white);display:flex;align-items:center;padding-left:23px;font-size:16px;color:#444}
.field.select::after{content:"";position:absolute;right:20px;top:27px;border-left:6px solid transparent;border-right:6px solid transparent;border-top:7px solid #222}
.submit{position:absolute;left:497px;top:660px;width:155px;height:46px;border:1.5px solid var(--white);color:var(--white);display:flex;align-items:center;justify-content:center;font:600 15px "Poppins",sans-serif}

/* footer */
.site-footer{position:absolute;left:0;top:3555px;width:1200px;height:289px;background:var(--footer);color:var(--white)}
.footer-logo{position:absolute;left:97px;top:50px;font-size:32px;color:var(--white);font-weight:600}
.footer-logo span{color:var(--white);font-weight:400}
.social{position:absolute;top:112px;width:36px;height:36px;border-radius:50%;background:#3a3a3a}
.col-head{position:absolute;top:54px;font-size:16px;font-weight:600;letter-spacing:.3px}
.col-item{position:absolute;font-size:14px}
.newsletter-input{position:absolute;left:778px;top:140px;width:319px;height:47px;background:var(--white);border-radius:3px;color:#555;font-size:13.5px;display:flex;align-items:center;padding-left:40px}
.copyright{position:absolute;left:0;top:253px;width:1200px;text-align:center;font-size:14.5px}
.to-top{position:absolute;left:1129px;top:207px;width:44px;height:44px;border-radius:50%;background:var(--blue);display:flex;align-items:center;justify-content:center}
</style>
</head>
<body>

<header class="site-header">
  <div class="logo brand">Tidewell <span>Comforts</span></div>
  <div class="nav active" style="left:553px">HOME</div>
  <div class="nav" style="left:632px">EVENTS</div>
  <div class="nav" style="left:723px">PRODUCTS</div>
  <div class="nav" style="left:840px">CONTACT</div>
  <div class="btn" style="left:943px;top:19px;width:156px;height:47px">Get a Quote</div>
</header>

<section class="hero">
  <div class="tile" style="left:0;top:0;background:linear-gradient(160deg,#6aa8e0,#1d8ad3 55%,#1f6f5c)" role="img" aria-label="Row of blue portable restrooms"></div>
  <div class="tile" style="left:243px;top:0;background:linear-gradient(180deg,#3b1a12,#c4541f 55%,#2a140f)" role="img" aria-label="Festival stage with fireworks"></div>
  <div class="tile" style="left:487px;top:0;background:linear-gradient(170deg,#6f8f5b,#e8ebe9 50%,#5e8a44)" role="img" aria-label="White restroom units at a garden event"></div>
  <div class="tile" style="left:728px;top:0;background:linear-gradient(170deg,#c7a46a,#d8c8b7 50%,#8e8f5d)" role="img" aria-label="Wedding couple outdoors"></div>
  <div class="tile" style="left:972px;top:0;background:linear-gradient(170deg,#b7a39a,#2b7fc4 55%,#4b8a3d)" role="img" aria-label="Long row of blue portable restrooms"></div>

  <div class="tile" style="left:0;top:246px;background:linear-gradient(170deg,#7aa6d6,#b9b9b9 50%,#57564f)" role="img" aria-label="Vintage silver trailer set up for an event"></div>
  <div class="tile" style="left:972px;top:246px;background:linear-gradient(160deg,#1d3560,#2f5a96 50%,#1a2236)" role="img" aria-label="Evening gathering under blue light"></div>

  <div class="tile" style="left:0;top:494px;background:linear-gradient(170deg,#b9c4cf,#1f84d3 45%,#c9ccd0)" role="img" aria-label="Blue portable restroom units"></div>
  <div class="tile" style="left:243px;top:494px;background:linear-gradient(170deg,#d9b074,#8e6a3d 50%,#5b4830)" role="img" aria-label="Friends toasting at a wine tasting"></div>
  <div class="tile" style="left:487px;top:494px;background:linear-gradient(170deg,#8fb1d0,#43a1c0 45%,#4b8f3c)" role="img" aria-label="Single restroom unit on a lawn"></div>
  <div class="tile" style="left:728px;top:494px;background:linear-gradient(170deg,#e2d7c7,#bba58a 50%,#6a7f8f)" role="img" aria-label="Team high-fiving in an office"></div>
  <div class="tile" style="left:972px;top:494px;background:linear-gradient(170deg,#8da5a0,#2384c9 50%,#2f7a5c)" role="img" aria-label="Restroom units near a building"></div>

  <div class="hero-copy">
    <div class="hero-title">Tidewell <span>Comforts</span></div>
    <p class="hero-text">Lorem ipsum dolor sit amet, consectetur adipiscing elit, sed do eiusmod<br>tempor incididunt ut labore et dolore magna aliqua.</p>
  </div>
  <div class="btn" style="left:522px;top:412px;width:156px;height:46px">Get Started</div>
</section>

<h2 class="section-title" style="top:880px">Our <span>Events</span></h2>

<svg class="arrow" style="left:62px" width="22" height="32" viewBox="0 0 22 32"><path d="M18 2 4 16l14 14" fill="none" stroke="#222" stroke-width="2"/></svg>
<svg class="arrow" style="left:1114px" width="22" height="32" viewBox="0 0 22 32"><path d="M4 2l14 14L4 30" fill="none" stroke="#222" stroke-width="2"/></svg>

<article class="event-card" style="left:100px">
  <div class="event-photo" style="background:linear-gradient(170deg,#e6e2e0,#d8b8be 45%,#8a6b6a)" role="img" aria-label="Wedding ceremony by a pool with balloons"></div>
  <div class="event-icon"><svg width="40" height="40" viewBox="0 0 40 40" fill="none" stroke="#fff" stroke-width="2"><circle cx="15" cy="24" r="9"/><circle cx="25" cy="24" r="9"/><path d="M12 12l3-5 3 5"/></svg></div>
  <h3 class="event-name">WEDDINGS</h3>
  <p class="event-text">Lorem ipsum dolor sit amet, consectetur acg elit, sed do eiusmod tempor incididunt ut labore et dolore magna aliqua.</p>
</article>
<article class="event-card" style="left:439px">
  <div class="event-photo" style="background:linear-gradient(170deg,#6b1d4e,#c46a54 50%,#3b1d2a)" role="img" aria-label="Friends celebrating at a private party"></div>
  <div class="event-icon"><svg width="40" height="40" viewBox="0 0 40 40" fill="none" stroke="#fff" stroke-width="2"><path d="M9 6h9l-1 10a4 4 0 0 1-7 0z"/><path d="M13.5 19v13M9 32h9"/><path d="M22 6h9l-1 10a4 4 0 0 1-7 0z"/><path d="M26.5 19v13M22 32h9"/></svg></div>
  <h3 class="event-name">PRIVATE PARTIES</h3>
  <p class="event-text">Lorem ipsum dolor sit amet, consectetur acg elit, sed do eiusmod tempor incididunt ut labore et dolore magna aliqua.</p>
</article>
<article class="event-card" style="left:778px">
  <div class="event-photo" style="background:linear-gradient(170deg,#9fbad6,#3c8fc0 40%,#e07b3a 65%,#5a5e5a)" role="img" aria-label="Colorful food truck on a city street"></div>
  <div class="event-icon"><svg width="42" height="40" viewBox="0 0 42 40" fill="none" stroke="#fff" stroke-width="2"><rect x="5" y="8" width="32" height="20" rx="2"/><path d="M9 14h24M10 19h22"/><circle cx="12" cy="31" r="3"/><circle cx="30" cy="31" r="3"/></svg></div>
  <h3 class="event-name">FOOD TRUCK</h3>
  <p class="event-text">Lorem ipsum dolor sit amet, consectetur acg elit, sed do eiusmod tempor incididunt ut labore et dolore magna aliqua.</p>
</article>

<div class="btn" style="left:506px;top:1408px;width:188px;height:47px">View All Events</div>

<section class="products">
  <h2 class="section-title" style="top:82px">Our <span>Products</span></h2>

  <article class="product-card" style="top:164px">
    <h3 class="product-name">TRAILER NAME</h3>
    <p class="product-text">Lorem ipsum dolor sit amet, consectetur adipiscilit, sed do eiusmod tempor incididunt ut labore et dolore magna aliqua. Quis um suspendisse ultrices gravida. Risus commodo viverra maecenas accumsan lacus vel facilisis. Lorem ipsum dolor sit amet, consectetur adipiscing elit, sed do eiusmod tempor incididunt ut labore et dolore magna aliqua.</p>
    <div class="btn">Learn More</div>
    <div class="product-photo" style="background:linear-gradient(170deg,#5b4a3a,#e9ecef 40%,#dfe3e6 60%,#6f6a62)" role="img" aria-label="White restroom trailer with steps"></div>
  </article>

  <article class="product-card" style="top:497px">
    <h3 class="product-name">TRAILER NAME</h3>
    <p class="product-text">Lorem ipsum dolor sit amet, consectetur adipiscilit, sed do eiusmod tempor incididunt ut labore et dolore magna aliqua. Quis um suspendisse ultrices gravida. Risus commodo viverra maecenas accumsan lacus vel facilisis. Lorem ipsum dolor sit amet, consectetur adipiscing elit, sed do eiusmod tempor incididunt ut labore et dolore magna aliqua.</p>
    <div class="btn">Learn More</div>
    <div class="product-photo" style="background:linear-gradient(180deg,#5d8fd2,#a9c6ea 35%,#e2c53a 55%,#6c6c6c 85%)" role="img" aria-label="Row of yellow portable restrooms"></div>
  </article>

  <article class="product-card" style="top:828px">
    <h3 class="product-name">TRAILER NAME</h3>
    <p class="product-text">Lorem ipsum dolor sit amet, consectetur adipiscilit, sed do eiusmod tempor incididunt ut labore et dolore magna aliqua. Quis um suspendisse ultrices gravida. Risus commodo viverra maecenas accumsan lacus vel facilisis. Lorem ipsum dolor sit amet, consectetur adipiscing elit, sed do eiusmod tempor incididunt ut labore et dolore magna aliqua.</p>
    <div class="btn">Learn More</div>
    <div class="product-photo" style="background:linear-gradient(120deg,#8fb2d8,#1f5fc4 45%,#2a7de0 65%,#4d8a3c)" role="img" aria-label="Line of blue portable restrooms on grass"></div>
  </article>
</section>

<section class="contact">
  <h2 class="contact-title">Contact Us</h2>
  <div class="field" style="left:233px;top:137px;width:734px">Name</div>
  <div class="field" style="left:233px;top:212px;width:734px">Email</div>
  <div class="field" style="left:233px;top:287px;width:734px">Phone</div>
  <div class="field select" style="left:233px;top:361px;width:358px">Type of Events</div>
  <div class="field select" style="left:609px;top:361px;width:358px">How Many People</div>
  <div class="field select" style="left:233px;top:436px;width:734px">Type Of Product You Are Interested In?</div>
  <div class="field select" style="left:233px;top:511px;width:358px">When Do You Need It?</div>
  <div class="field select" style="left:609px;top:511px;width:358px">For How Long?</div>
  <div class="field select" style="left:233px;top:585px;width:734px">Where</div>
  <div class="submit">SUBMIT</div>
</section>

<footer class="site-footer">
  <div class="footer-logo">Tidewell <span>Comforts</span></div>
  <div class="social" style="left:125px"></div>
  <div class="social" style="left:169px"></div>
  <div class="social" style="left:212px"></div>
  <div class="social" style="left:255px"></div>

  <div class="col-head" style="left:387px">QUICK LINKS</div>
  <div class="col-item" style="left:387px;top:88px">Home</div>
  <div class="col-item" style="left:387px;top:115px">Event</div>
  <div class="col-item" style="left:387px;top:142px">Products</div>
  <div class="col-item" style="left:387px;top:169px">Contact</div>

  <div class="col-head" style="left:545px">CONTACT INFO</div>
  <div class="col-item" style="left:545px;top:88px">123 Your Adress Goes Here.</div>
  <div class="col-item" style="left:545px;top:115px">CA, 1234567</div>
  <div class="col-item" style="left:545px;top:142px">888 888 8888</div>
  <div class="col-item" style="left:545px;top:169px">info@tidewellcomforts.com</div>

  <div class="col-head" style="left:778px">NEWSLETTER</div>
  <div class="col-item" style="left:778px;top:88px;width:330px;line-height:24px">For news, events and updates, subscribe to our newsletter.</div>
  <div class="newsletter-input">Enter your email</div>
  <svg class="abs" style="left:795px;top:157px" width="16" height="13" viewBox="0 0 16 13"><rect x="0.5" y="0.5" width="15" height="12" fill="#555"/><path d="M1 1l7 6 7-6" fill="none" stroke="#fff" stroke-width="1.3"/></svg>
  <svg class="abs" style="left:1060px;top:155px" width="18" height="18" viewBox="0 0 18 18"><path d="M17 1 1 8l6 2 2 6z" fill="#2a87d7"/></svg>

  <div class="copyright">©2022 Tidewell Comforts. All Rights Reserved.</div>
  <div class="to-top"><svg width="16" height="20" viewBox="0 0 16 20"><path d="M8 18V3M2 8l6-6 6 6" fill="none" stroke="#fff" stroke-width="2.2"/></svg></div>
</footer>

</body>
</html>
```